Valdo Capital

We need a corporate style website design for a new company based in Shenzhen's Qianhai Special Economic Development Zone, China. We provide a range of financial services to large international investment companies. Typically these companies invest over 5 million RMB. The company is part of a group that consists of NorthKilns, ValdoTrusts and ValdoEquity. Our location and gateway into Qianhai Special Economic Zone is our core advantage. We would like to see designs that Do Not use purple and orange. The website design should be similar to other websites in this family but different enough to give it a unique style (See attached website links for reference). The final design should communicate financial safety and growth. This website will act partly as a business chamber with connections to the government so we would like it to be diplomatic in style.

www.northkilns.example
www.valdotrusts.example

*Nevegation Bar
Should including Homepage, Financial Product, Team, News.
Could refer to www.valdotrusts.example

*Contact Details

Miss Lan
Address:E 728, North Block, KMO Centre, East Sector, Shenzhen Bright Science Campus
Telephone: +86 0755 63920417
Cellphone: +86 13957280316

* Social Media
Should be grouped like:
1. Weibo QRcode+ Weibo
2. Facebook, Twitter, Linkedin.

Industry/Entity Type

Investment

```html
<!DOCTYPE html>
<html lang="en">
<head>
<meta charset="utf-8">
<title>Valdo Capital</title>
<link rel="stylesheet" href="https://fonts.googleapis.com/css2?family=Montserrat:wght@400;500;600&family=Open+Sans:wght@400;600&display=swap">
<style>
  :root {
    --blue: #29a9e1;
    --brown: #5b3620;
    --ink: #2d2d2d;
    --text: #555555;
    --muted: #7c7c7c;
    --hero-bg: #f2f1ef;
    --panel-bg: #f6f6f6;
    --line: #e4e4e4;
    --dark: #262626;
    --footer: #000000;
    --white: #ffffff;
  }
  * { box-sizing: border-box; margin: 0; padding: 0; }
  html, body { width: 1147px; height: 1200px; overflow: hidden; }
  body {
    position: relative;
    background: var(--white);
    font-family: "Open Sans", Arial, sans-serif;
    color: var(--text);
  }
  .abs { position: absolute; }

  /* header */
  .top-bar { left: 0; top: 0; width: 1147px; height: 5px; background: var(--blue); }
  .site-header { left: 0; top: 5px; width: 1147px; height: 114px; background: var(--white); }
  .brand { left: 115px; top: 38px; display: flex; align-items: center; gap: 14px; }
  .brand-mark { width: 40px; height: 40px; border-radius: 50%; background: var(--blue); }
  .brand-name { font-family: "Open Sans", sans-serif; font-weight: 600; font-size: 30px; color: var(--ink); letter-spacing: .5px; }
  .main-nav { left: 659px; top: 5px; height: 114px; display: flex; }
  .main-nav a {
    display: block; height: 114px; line-height: 118px; text-decoration: none;
    font-size: 14px; color: #4a4a4a; padding: 0 17px;
  }
  .main-nav a.current { background: #f4f4f4; color: var(--blue); border-bottom: 5px solid var(--blue); width: 90px; text-align: center; padding: 0; line-height: 123px; margin-right: 0; }

  /* hero */
  .hero { left: 0; top: 119px; width: 1147px; height: 386px; background: var(--hero-bg); border-bottom: 1px solid #e6e5e3; }
  .hero-title { left: 124px; top: 186px; font-family: "Montserrat", sans-serif; font-weight: 500; font-size: 25px; line-height: 33px; color: var(--brown); }
  .hero-sub { left: 124px; top: 258px; font-family: "Montserrat", sans-serif; font-size: 19px; color: var(--blue); }
  .hero-text { left: 125px; top: 294px; width: 285px; font-size: 10.5px; line-height: 18px; color: var(--muted); }
  .btn {
    display: flex; align-items: center; justify-content: center; gap: 6px;
    width: 130px; height: 36px; background: var(--dark); color: var(--white);
    border-radius: 3px; font-size: 14px; text-decoration: none;
  }
  .hero .btn, .btn.hero-btn { left: 125px; top: 388px; }
  .hero-photo {
    left: 497px; top: 171px; width: 525px; height: 293px;
    background: linear-gradient(120deg, #2a2523 0%, #6a5a52 30%, #dfe4ec 52%, #bcc3cf 62%, #3a3a42 80%, #1d1d22 100%);
    box-shadow: 0 10px 18px rgba(0,0,0,.18);
  }

  /* services */
  .service { top: 552px; width: 300px; display: flex; gap: 13px; }
  .service-icon { width: 59px; height: 59px; border-radius: 50%; flex: none; display: flex; align-items: center; justify-content: center; }
  .service-icon.blue { background: var(--blue); }
  .service-icon.dark { background: #3d3d3d; }
  .service h3 { font-family: "Montserrat", sans-serif; font-weight: 500; font-size: 19px; color: var(--ink); margin-top: 9px; }
  .service p { font-size: 12px; line-height: 16.5px; color: var(--muted); margin-top: 3px; width: 210px; }
  .read-more { display: inline-flex; align-items: center; gap: 6px; font-size: 12px; color: var(--blue); text-decoration: none; margin-top: 4px; }

  /* banner */
  .banner { left: 123px; top: 692px; width: 900px; height: 117px; background: var(--panel-bg); border: 1px solid var(--line); border-top: 4px solid var(--blue); box-shadow: 0 14px 16px -12px rgba(0,0,0,.25); }
  .banner h2 { position: absolute; left: 31px; top: 18px; font-weight: 400; font-size: 26px; color: var(--ink); }
  .banner p { position: absolute; left: 33px; top: 62px; width: 640px; font-size: 15px; line-height: 19px; color: var(--ink); }
  .banner .btn { position: absolute; left: 737px; top: 35px; }

  /* section headings */
  .section-title { font-family: "Montserrat", sans-serif; font-weight: 500; font-size: 18px; color: var(--ink); display: flex; align-items: center; gap: 10px; }
  .section-title::after { content: ""; flex: 1; height: 3px; border-top: 1px solid var(--line); border-bottom: 1px solid var(--line); }
  .news-title { left: 123px; top: 864px; width: 595px; }
  .testi-title { left: 735px; top: 864px; width: 258px; }
  .testi-arrows { left: 996px; top: 867px; display: flex; gap: 2px; }

  /* news */
  .news-photo { top: 910px; width: 288px; height: 111px; }
  .news-photo.one { left: 123px; background: linear-gradient(90deg, #3b4150 0%, #c9ccd2 40%, #e9ecef 65%, #2e3138 100%); }
  .news-photo.two { left: 430px; background: linear-gradient(90deg, #cfd6dc 0%, #23262b 30%, #e4e7ea 55%, #22252a 80%, #d6dbe0 100%); }
  .news-tag { top: 1032px; width: 43px; height: 71px; display: flex; align-items: center; justify-content: center; }
  .news-tag.blue { left: 124px; background: var(--blue); }
  .news-tag.light { left: 431px; background: #f7f7f7; border: 1px solid var(--line); }
  .news-item { top: 1030px; width: 240px; }
  .news-item h4 { font-family: "Montserrat", sans-serif; font-weight: 500; font-size: 16px; color: var(--ink); margin-left: 1px; }
  .news-meta { font-size: 12px; color: var(--blue); margin-top: 2px; }
  .news-meta span { color: var(--muted); }
  .news-item p { font-size: 12px; color: var(--ink); margin-top: 8px; }

  /* testimonial */
  .testimonial { left: 736px; top: 909px; width: 287px; height: 181px; border: 1px solid var(--line); }
  .testimonial h4 { position: absolute; left: 22px; top: 25px; font-family: "Montserrat", sans-serif; font-weight: 600; font-size: 15.5px; color: var(--blue); }
  .testimonial p { position: absolute; left: 21px; top: 56px; width: 250px; font-size: 11.5px; line-height: 17.5px; color: var(--muted); }
  .quote-mark { position: absolute; left: 223px; top: 96px; font-family: Georgia, serif; font-size: 110px; line-height: 1; color: #ececec; }
  .author { position: absolute; left: 125px; top: 130px; }
  .author strong { display: block; font-family: "Montserrat", sans-serif; font-size: 14px; font-weight: 600; color: #111; }
  .author span { font-family: "Montserrat", sans-serif; font-size: 13px; font-weight: 600; color: #b5b5b5; }
  .avatar-ring { left: 755px; top: 1024px; width: 96px; height: 96px; border-radius: 50%; background: var(--white); border: 1px solid #e2e2e2; box-shadow: 0 2px 6px rgba(0,0,0,.12); display: flex; align-items: center; justify-content: center; }
  .avatar { width: 80px; height: 80px; border-radius: 50%; background: radial-gradient(circle at 50% 45%, #29a9e1 0 45%, #f4f4f4 46%); }

  /* footer */
  .site-footer { left: 0; top: 1156px; width: 1147px; height: 44px; background: var(--footer); color: var(--white); font-size: 11px; }
  .site-footer .copy { position: absolute; left: 123px; top: 15px; }
  .site-footer .legal { position: absolute; right: 124px; top: 15px; }
</style>
</head>
<body>
  <div class="abs top-bar"></div>
  <header class="abs site-header"></header>
  <div class="abs brand">
    <span class="brand-mark"></span>
    <span class="brand-name">Valdo Capital</span>
  </div>
  <nav class="abs main-nav">
    <a class="current" href="#">Home</a>
    <a href="#">Financial Products</a>
    <a href="#">Team</a>
    <a href="#">News</a>
  </nav>

  <section class="abs hero"></section>
  <h1 class="abs hero-title">WELCOME TO<br>VALDO CAPITAL.COM</h1>
  <p class="abs hero-sub">Lorem ipsum dolor sit amet</p>
  <p class="abs hero-text">Lorem ipsum dolor sit amet, consectetur adipisicing elit, sed do eiusmod tempor incididunt ut labore et dolore magna aliqua. Ut enim ad minim veniam, quis nostrud exercitation ullamco laboris.</p>
  <a class="abs btn hero-btn" href="#">Learn More
    <svg width="10" height="10" viewBox="0 0 10 10"><path d="M1 1l4 4-4 4M5 1l4 4-4 4" fill="none" stroke="#fff" stroke-width="1.6"/></svg>
  </a>
  <div class="abs hero-photo" role="img" aria-label="Business meeting with a hand holding a pen over printed financial charts"></div>

  <div class="abs service" style="left:121px">
    <div class="service-icon blue">
      <svg width="34" height="26" viewBox="0 0 34 26" fill="#fff"><circle cx="17" cy="7" r="5"/><circle cx="7" cy="9" r="4"/><circle cx="27" cy="9" r="4"/><path d="M9 25c0-7 3.5-10 8-10s8 3 8 10z"/><path d="M0 24c0-5 3-8 7-8 1.5 0 2.6.4 3.5 1-2 2-3 4.5-3 7z"/><path d="M34 24c0-5-3-8-7-8-1.5 0-2.6.4-3.5 1 2 2 3 4.5 3 7z"/></svg>
    </div>
    <div>
      <h3>Consultancy</h3>
      <p>Lorem ipsum dolor sit amet, consec adipisicing elit, sed do eiusmod ut labore et dolore magna aliqua.</p>
      <a class="read-more" href="#">Read More <svg width="16" height="8" viewBox="0 0 16 8"><path d="M0 4h14M11 1l3 3-3 3" fill="none" stroke="#29a9e1" stroke-width="1.3"/></svg></a>
    </div>
  </div>
  <div class="abs service" style="left:439px">
    <div class="service-icon dark">
      <svg width="32" height="30" viewBox="0 0 32 30" fill="#fff"><rect x="3" y="20" width="4" height="9"/><rect x="10" y="16" width="4" height="13"/><rect x="17" y="12" width="4" height="17"/><rect x="24" y="8" width="4" height="21"/><path d="M3 16l8-6 6 4 11-10" fill="none" stroke="#fff" stroke-width="2"/><text x="2" y="10" font-size="11" font-family="Arial" font-weight="700">$</text></svg>
    </div>
    <div>
      <h3>Finance</h3>
      <p>Lorem ipsum dolor sit amet, consec adipisicing elit, sed do eiusmod ut labore et dolore magna aliqua.</p>
      <a class="read-more" href="#">Read More <svg width="16" height="8" viewBox="0 0 16 8"><path d="M0 4h14M11 1l3 3-3 3" fill="none" stroke="#29a9e1" stroke-width="1.3"/></svg></a>
    </div>
  </div>
  <div class="abs service" style="left:756px">
    <div class="service-icon dark">
      <svg width="32" height="28" viewBox="0 0 32 28" fill="#fff"><path d="M16 1L1 14h4v13h8v-8h6v8h8V14h4z"/></svg>
    </div>
    <div>
      <h3>Property Management</h3>
      <p>Lorem ipsum dolor sit amet, consec adipisicing elit, sed do eiusmod ut labore et dolore magna aliqua.</p>
      <a class="read-more" href="#">Read More <svg width="16" height="8" viewBox="0 0 16 8"><path d="M0 4h14M11 1l3 3-3 3" fill="none" stroke="#29a9e1" stroke-width="1.3"/></svg></a>
    </div>
  </div>

  <section class="abs banner">
    <h2>We Provide a Range Of Financial Services</h2>
    <p>Lorem ipsum dolor sit amet, consectetur adipisicing elit, sed do eiusmod tempor incididunt ut labore et dolore magna aliqua.</p>
    <a class="btn" href="#">Learn More
      <svg width="10" height="10" viewBox="0 0 10 10"><path d="M1 1l4 4-4 4M5 1l4 4-4 4" fill="none" stroke="#fff" stroke-width="1.6"/></svg>
    </a>
  </section>

  <h3 class="abs section-title news-title">Latest News</h3>
  <h3 class="abs section-title testi-title">Testimonials</h3>
  <div class="abs testi-arrows">
    <svg width="14" height="18" viewBox="0 0 14 18"><path d="M11 2L4 9l7 7" fill="none" stroke="#b9b9b9" stroke-width="2.2"/></svg>
    <svg width="14" height="18" viewBox="0 0 14 18"><path d="M3 2l7 7-7 7" fill="none" stroke="#29a9e1" stroke-width="2.2"/></svg>
  </div>

  <div class="abs news-photo one" role="img" aria-label="Group of business people in suits standing together"></div>
  <div class="abs news-photo two" role="img" aria-label="Young professionals in dark suits posing as a team"></div>

  <div class="abs news-tag blue">
    <svg width="22" height="18" viewBox="0 0 22 18"><rect x="1" y="1" width="20" height="16" fill="none" stroke="#fff" stroke-width="2"/><path d="M3 15l5-6 4 4 3-3 4 5z" fill="#fff"/><circle cx="15" cy="6" r="2" fill="#fff"/></svg>
  </div>
  <div class="abs news-item" style="left:189px">
    <h4>Lorem ipsum dolor sit</h4>
    <div class="news-meta">Dec 12,2012 <span>|</span> by Marcus <span>|</span> 12 Comments</div>
    <p>Lorem ipsum dolor sit amet, consectetur</p>
    <a class="read-more" href="#">Read More <svg width="16" height="8" viewBox="0 0 16 8"><path d="M0 4h14M11 1l3 3-3 3" fill="none" stroke="#29a9e1" stroke-width="1.3"/></svg></a>
  </div>

  <div class="abs news-tag light">
    <svg width="24" height="24" viewBox="0 0 24 24"><circle cx="11" cy="11" r="8" fill="none" stroke="#29a9e1" stroke-width="3.5"/><path d="M15 15l6 6" stroke="#29a9e1" stroke-width="3.5"/></svg>
  </div>
  <div class="abs news-item" style="left:495px">
    <h4>Lorem ipsum dolor sit</h4>
    <div class="news-meta">Dec 12,2012 <span>|</span> by Marcus <span>|</span> 12 Comments</div>
    <p>Lorem ipsum dolor sit amet, consectetur</p>
    <a class="read-more" href="#">Read More <svg width="16" height="8" viewBox="0 0 16 8"><path d="M0 4h14M11 1l3 3-3 3" fill="none" stroke="#29a9e1" stroke-width="1.3"/></svg></a>
  </div>

  <section class="abs testimonial">
    <h4>Lorem ipsum dolor sit amet</h4>
    <p>Lorem ipsum dolor slo onsec nelioro tue raliquet Morbi nec In Curabitur, lorem in design Morbi nec In Curabitur lreaoreet nisl</p>
    <span class="quote-mark">&#8221;</span>
    <div class="author"><strong>Daniel Harper</strong><span>Manager</span></div>
  </section>
  <div class="abs avatar-ring"><div class="avatar" role="img" aria-label="Client portrait placeholder"></div></div>

  <footer class="abs site-footer">
    <span class="copy">Copyright &copy; 2014 Valdo Capital. All Rights Reserved</span>
    <span class="legal">Privacy Policy &amp; Term of Uses</span>
  </footer>
</body>
</html>
```